Foot and ankle surgeon requires a website design

I need a website where prospective and established patients can obtain information and then direct them to making appointments. My practice is a highly professional surgical practice specialising in surgery to the foot and ankle. My title is Mr Colin Brasket, Podiatric Foot & Ankle Surgeon. My qualifications are: BSc MSc FACPS
The practice website will require information on: Locations, phone numbers to make appointments, general background on podiatric surgery,
I would like to include information on: my hospital appointments, surgical fellowships held, training programs undertaken, association memberships, publications written, links to useful websites
A page dedicated to common foot conditions would be useful and also a page with referral information including an online registration section that will be sent direct to the receptionist.
Examples of similar websites include:
http://www.dorvelquintaro.com.au/
http://www.haldenfootsurgeon.com.au/
I will provide files on logo, self photos and my personal training history etc.
Also if there is going to be a background theme I personally am associated with surfing and beach activities, it would be great if this was able to be reflected in the design.
Thank you.

```html
<!DOCTYPE html>
<html lang="en">
<head>
<meta charset="utf-8">
<title>Mr Colin Brasket – Podiatric Foot &amp; Ankle Surgeon</title>
<link rel="stylesheet" href="https://fonts.googleapis.com/css2?family=Arimo:wght@400;700&family=Roboto+Condensed:wght@400;700&family=PT+Serif:wght@400;700&display=swap">
<style>
:root{
  --orange:#e8780f;
  --orange-dark:#c05f05;
  --navy:#0d3f72;
  --nav-navy:#17375e;
  --text:#8a8a8a;
  --text-dark:#555;
  --band:#eef0f4;
  --line:#d9dde3;
  --footer:#3b3b3b;
  --footer-text:#c9c9c9;
}
*{box-sizing:border-box;margin:0;padding:0}
html,body{width:1200px;height:2169px;overflow:hidden;background:#fff}
body{font-family:Arimo,Arial,sans-serif;color:var(--text);position:relative}
.abs{position:absolute}
.topline{position:absolute;left:0;top:0;width:1200px;height:3px;background:var(--orange)}

/* header */
.brand{left:136px;top:66px}
.brand-name{font-family:"PT Serif",Georgia,serif;font-weight:700;font-size:22px;color:var(--navy);line-height:1}
.brand-sub{font-family:"PT Serif",Georgia,serif;font-size:11px;color:var(--orange);margin-top:4px}
.ring{width:50px;height:50px;border:3px solid var(--navy);border-radius:50%;display:flex;align-items:center;justify-content:center}
.contact-title{font-family:"Roboto Condensed",sans-serif;font-size:13px;color:var(--navy);white-space:nowrap}
.contact-line{font-size:10px;color:var(--text);line-height:16px;display:flex;gap:8px;white-space:nowrap}
.contact-line svg{flex:none;margin-top:3px}
.phone-big{font-family:"Roboto Condensed",sans-serif;font-weight:700;font-size:30px;color:var(--orange);white-space:nowrap}

/* nav */
.nav{left:132px;top:150px;width:938px;height:53px;background:var(--orange);display:flex;align-items:center}
.nav a{font-family:"PT Serif",Georgia,serif;font-size:14px;color:#fff;text-decoration:none;height:53px;line-height:53px;padding:0 14px 0 15px;white-space:nowrap}
.nav a.active{background:var(--nav-navy)}

/* hero */
.hero{left:132px;top:207px;width:938px;height:433px;background:linear-gradient(120deg,#f1e9ea 0%,#e2c9c3 35%,#d9b5a9 55%,#efe4e3 100%)}
.caption{left:132px;top:564px;width:938px;height:76px;background:rgba(110,110,115,.72)}
.caption-text{left:155px;top:590px;font-family:"Roboto Condensed",sans-serif;font-size:26px;color:#fff;letter-spacing:.2px}
.arrowbox{width:23px;height:23px;background:#4a4a4a;display:flex;align-items:center;justify-content:center}

/* intro */
.intro{left:132px;top:640px;width:938px;height:123px;border:1px solid var(--line);border-top:none}
.intro h2{position:absolute;left:8px;top:22px;font-size:20px;font-weight:700;color:var(--navy);white-space:nowrap}
.intro h2 span{font-size:14px;font-weight:400;color:var(--orange)}
.intro p{position:absolute;left:9px;top:62px;width:655px;font-size:11px;line-height:20px;color:var(--text)}
.btn-navy{position:absolute;left:716px;top:41px;width:195px;height:49px;background:var(--navy);color:#fff;font-weight:700;font-size:19px;display:flex;align-items:center;justify-content:center}

/* welcome */
.welcome{left:130px;top:780px;width:625px}
.welcome h2{font-size:17px;font-weight:700;color:var(--navy);margin-bottom:16px}
.welcome .lead{font-size:11px;line-height:21px;color:var(--orange);margin-bottom:12px}
.welcome p{font-size:11px;line-height:21px;color:var(--text-dark);margin-bottom:10px}
.btn-orange{background:var(--orange);color:#fff;font-size:14px;display:flex;align-items:center;justify-content:center;border-bottom:3px solid var(--orange-dark);white-space:nowrap}

.appt{left:784px;top:785px;width:286px;height:408px;border:1px solid var(--line);padding:10px}
.appt-inner{width:264px;height:386px;border:1px solid var(--line);background:#f7f8fa;position:relative;overflow:hidden}
.appt h3{position:absolute;left:24px;top:28px;font-weight:400;font-size:19px;color:var(--navy);white-space:nowrap}
.field{position:absolute;left:14px;width:238px;height:36px;background:#fff;border:1px solid #e1e4e8;font-size:10px;color:#aaa;padding:11px 9px}
.appt-btn{position:absolute;left:51px;top:329px;width:161px;height:43px}

/* features */
.band{left:0;top:1218px;width:1200px;height:397px;background:var(--band)}
.spec-small{left:132px;top:1245px;font-size:17px;font-weight:700;color:var(--navy)}
.spec-big{left:132px;top:1270px;font-size:21px;font-weight:700;color:var(--orange)}
.spec-text{left:132px;top:1311px;width:250px;font-size:11px;line-height:25px;color:var(--text)}
.feature{width:245px}
.feature h4{font-family:"Roboto Condensed",sans-serif;font-weight:400;font-size:15px;color:var(--orange);margin-bottom:8px}
.feature p{font-size:11px;line-height:22px;color:var(--text)}

/* conditions */
.cond-title{left:132px;top:1651px;font-size:19px;font-weight:700;color:var(--navy)}
.cond-lead{left:132px;top:1688px;width:940px;font-size:11px;line-height:21px;color:var(--orange)}
.cond-item{font-size:11px;color:var(--text-dark);display:flex;align-items:center;gap:13px;white-space:nowrap}

/* footer */
.footer{left:0;top:1847px;width:1200px;height:322px;background:var(--footer)}
.f-head{font-family:"PT Serif",Georgia,serif;font-size:16px;color:#fff}
.f-text{font-size:10px;line-height:19px;color:var(--footer-text)}
.f-input{width:242px;height:37px;border:1px solid #888;font-size:10px;color:#bbb;padding:12px 10px}
.f-btn{left:142px;top:2053px;width:120px;height:38px;border:1px solid #ddd;color:#fff;font-family:"PT Serif",Georgia,serif;font-size:13px;display:flex;align-items:center;justify-content:center}
.f-list li{list-style:none;font-size:10px;color:var(--footer-text);display:flex;align-items:center;gap:10px;height:27.5px;white-space:nowrap}
.f-list li::before{content:"";width:5px;height:5px;border-radius:50%;background:#ccc}
.f-rule{left:142px;top:2107px;width:916px;height:1px;background:#575757}
.social{width:32px;height:32px;border:2px solid #9a9a9a;border-radius:50%}
</style>
</head>
<body>
<div class="topline"></div>

<!-- header -->
<div class="abs brand">
  <div class="brand-name">Mr Colin Brasket</div>
  <div class="brand-sub">Podiatric Foot &amp; Ankle Surgeon</div>
</div>

<div class="abs ring" style="left:490px;top:43px">
  <svg width="22" height="22" viewBox="0 0 24 24"><path d="M12 2a7 7 0 0 0-7 7c0 5 7 13 7 13s7-8 7-13a7 7 0 0 0-7-7z" fill="#e8780f"/><circle cx="12" cy="9" r="2.6" fill="#fff"/></svg>
</div>
<div class="abs" style="left:557px;top:44px">
  <div class="contact-title">Want to Meet &amp; Talk Directly? Find Us Here</div>
  <div style="margin-top:5px">
    <div class="contact-line"><svg width="9" height="9" viewBox="0 0 10 10"><path d="M5 0 0 5h1.5v5h7V5H10z" fill="#e8780f"/></svg><span>Address :42 Seabreeze Parade, Coastal Road,<br>PO BOX 7720,Harbourton WA 6611</span></div>
    <div class="contact-line" style="margin-top:4px"><svg width="9" height="9" viewBox="0 0 10 10"><rect y="1.5" width="10" height="7" fill="#e8780f"/></svg><span>Email:www.cfag-clinic.com</span></div>
  </div>
</div>

<div class="abs ring" style="left:800px;top:43px">
  <svg width="22" height="22" viewBox="0 0 24 24"><path d="M6.6 10.8a15 15 0 0 0 6.6 6.6l2.2-2.2a1 1 0 0 1 1-.25 11 11 0 0 0 3.6.6 1 1 0 0 1 1 1V20a1 1 0 0 1-1 1A17 17 0 0 1 3 4a1 1 0 0 1 1-1h3.5a1 1 0 0 1 1 1c0 1.250.2 2.45.6 3.6a1 1 0 0 1-.25 1z" fill="#e8780f"/></svg>
</div>
<div class="abs" style="left:862px;top:44px">
  <div class="contact-title">Need Help From Us? Feel Free to Call Us</div>
  <div class="phone-big">(089)-555-0182</div>
</div>

<nav class="abs nav">
  <a class="active" href="#">Home</a>
  <a href="#">Appointments</a>
  <a href="#">Surgical Fellowships</a>
  <a href="#">Training Programs</a>
  <a href="#">Memberships</a>
  <a href="#">Publications</a>
  <a href="#">Useful websites</a>
  <a href="#">Contact us</a>
</nav>

<!-- hero -->
<div class="abs hero" role="img" aria-label="Photo of a podiatrist treating a patient's foot"></div>
<div class="abs caption"></div>
<div class="abs caption-text">PODIATRIC FOOT &amp; ANKLE SURGEON</div>
<div class="abs arrowbox" style="left:1006px;top:593px"><svg width="8" height="10" viewBox="0 0 8 10"><path d="M6 1 2 5l4 4" stroke="#fff" stroke-width="2" fill="none"/></svg></div>
<div class="abs arrowbox" style="left:1035px;top:593px"><svg width="8" height="10" viewBox="0 0 8 10"><path d="M2 1l4 4-4 4" stroke="#fff" stroke-width="2" fill="none"/></svg></div>

<div class="abs intro">
  <h2>SPECIALIST PODIATRIC SURGEON <span>Reconstructive Foot Surgery</span></h2>
  <p>Advances in foot surgery over the past 20-years have significantly improved outcomes and the quality of life for people with painful foot disorders. Innovations in medical devices, surgical techniques and functional.....</p>
  <div class="btn-navy">FIND OUT MORE</div>
</div>

<!-- welcome -->
<section class="abs welcome">
  <h2>WELCOME TO COLIN BRASKET</h2>
  <p class="lead">The Coastal Foot and Ankle Group strive to provide exceptional service and care to all patients, young and old, to ensure they enjoy a pain free lifestyle.Group strive to provide exceptional service and care to all patients, young and old, to ensure they enjoy a pain free lifestyle.</p>
  <p>For those unfamiliar with our services, we are a team of accredited health professionals dealing with the prevention, diagnosis, treatment and rehabilitation of medical and surgical conditions related to feet, ankles and lower limbs.</p>
  <p>The Coastal Foot and Ankle Group have practices based throughout regional Western Australia in Port Calder and Redstone and offer the following services; sports injuries, foot care, foot orthoses and diabetes care.</p>
  <p>Many foot and lower limb problems, if identified early can be prevented, so take the right step and contact the Coastal Foot and Ankle Group for advice on your foot, ankle, heel or leg pain or sports injury.Many foot and lower limb problems, if identified early can be prevented, so take the right step and contact the Coastal Foot and Ankle Group for advice on your foot, ankle, heel or leg pain or sports injury...</p>
</section>
<div class="abs btn-orange" style="left:132px;top:1125px;width:224px;height:46px">CLICK HERE FOR MORE INFO</div>

<aside class="abs appt">
  <div class="appt-inner">
    <h3>GET AN APPOINTMENT</h3>
    <div class="field" style="top:66px">NAME :</div>
    <div class="field" style="top:108px">EMAIL :</div>
    <div class="field" style="top:150px">PHONE :</div>
    <div class="field" style="top:192px">APPOINTMENT DATE :</div>
    <div class="field" style="top:234px;height:81px">MESSAGE :</div>
    <div class="btn-orange appt-btn">SUBMIT REQUEST</div>
  </div>
</aside>

<!-- features -->
<div class="abs band"></div>
<div class="abs spec-small">SPECIALIST</div>
<div class="abs spec-big">PODIATRIC SURGEON</div>
<div class="abs spec-text">
  <p>Advances in foot surgery over the past 20-years have significantly improved outcomes and the quality of life for people with painful foot disorders. Innovations in medical devices, surgical techniques and functional.....</p>
  <p style="margin-top:12px">Outcomes and the quality of life for people with painful foot disorders. Innovations in medical surgical techniques and functional.....</p>
</div>
<div class="abs btn-orange" style="left:132px;top:1540px;width:151px;height:46px;font-size:15px">VIEW ALL</div>

<svg class="abs" style="left:403px;top:1262px" width="50" height="50" viewBox="0 0 50 50"><rect x="6" y="10" width="30" height="30" rx="6" transform="rotate(-35 21 25)" fill="none" stroke="#777" stroke-width="3"/><circle cx="14" cy="18" r="3" fill="#777"/></svg>
<div class="abs feature" style="left:466px;top:1277px"><h4>SURGICAL FELLOWSHIPS</h4><p>Advances in foot surgery over the past 20-years have significantly improved outcomes and the quality of life for people with painful foot disor techniques and functional ...</p></div>

<svg class="abs" style="left:762px;top:1262px" width="50" height="50" viewBox="0 0 50 50"><path d="M6 44h38M10 44V30l10-8 8 6 10-16" fill="none" stroke="#777" stroke-width="4"/><circle cx="38" cy="9" r="4" fill="#777"/></svg>
<div class="abs feature" style="left:826px;top:1277px"><h4>TRAINING PROGRAMS</h4><p>Advances in foot surgery over the past 20-years have significantly improved outcomes and the quality of life for people with painful foot disor techniques and functional ...</p></div>

<svg class="abs" style="left:405px;top:1447px" width="46" height="46" viewBox="0 0 46 46"><circle cx="18" cy="13" r="8" fill="#666"/><path d="M2 42c0-10 7-16 16-16s16 6 16 16z" fill="#666"/><path d="M36 26v12M30 32h12" stroke="#666" stroke-width="3"/></svg>
<div class="abs feature" style="left:466px;top:1460px"><h4>MEMBERSHIPS</h4><p>Advances in foot surgery over the past 20-years have significantly improved outcomes and the quality of life for people with painful foot disor techniques and functional ...</p></div>

<svg class="abs" style="left:768px;top:1457px" width="42" height="42" viewBox="0 0 42 42"><rect x="1" y="1" width="40" height="40" rx="8" fill="#666"/><rect x="12" y="8" width="16" height="14" fill="#fff" transform="rotate(12 20 15)"/><rect x="10" y="29" width="22" height="4" fill="#ddd"/></svg>
<div class="abs feature" style="left:826px;top:1460px"><h4>SURGICAL FELLOWSHIPS</h4><p>Advances in foot surgery over the past 20-years have significantly improved outcomes and the quality of life for people with painful foot disor techniques and functional ...</p></div>

<!-- conditions -->
<div class="abs cond-title">FOOT CONDITIONS</div>
<div class="abs cond-lead">Mea an qualisque molestiae, te quem aperiam invidunt ius. No recteque facilisis vix, his magna omnium concludaturque id. Id audiam maiorum consequuntu Mea an qualisque molestiae, te quem aperiam invidunt ius. No recteque facilisis vix, his magna omnium concludaturque id. Id audiam maiorum consequuntu.............</div>

<svg width="0" height="0" style="position:absolute"><defs><symbol id="arr" viewBox="0 0 12 10"><path d="M0 4h7V1l5 4-5 4V6H0z" fill="#888"/></symbol></defs></svg>
<div class="abs cond-item" style="left:134px;top:1766px"><svg width="12" height="10"><use href="#arr"/></svg>Bunions</div>
<div class="abs cond-item" style="left:134px;top:1796px"><svg width="12" height="10"><use href="#arr"/></svg>Tailors Bunion Deformity</div>
<div class="abs cond-item" style="left:379px;top:1766px"><svg width="12" height="10"><use href="#arr"/></svg>Hammertoe Deformity</div>
<div class="abs cond-item" style="left:379px;top:1796px"><svg width="12" height="10"><use href="#arr"/></svg>Ingrown Toenails</div>
<div class="abs cond-item" style="left:626px;top:1766px"><svg width="12" height="10"><use href="#arr"/></svg>Big Toe Joint Arthritis</div>
<div class="abs cond-item" style="left:626px;top:1796px"><svg width="12" height="10"><use href="#arr"/></svg>Ganglions</div>
<div class="abs cond-item" style="left:868px;top:1766px"><svg width="12" height="10"><use href="#arr"/></svg>Neuroma</div>
<div class="abs cond-item" style="left:868px;top:1796px"><svg width="12" height="10"><use href="#arr"/></svg>Painful little toes</div>

<!-- footer -->
<footer class="abs footer"></footer>
<div class="abs f-head" style="left:142px;top:1871px">Newsletter</div>
<div class="abs f-text" style="left:142px;top:1910px;width:270px">You don't need to change your current system to use the Tidewell.</div>
<div class="abs f-input" style="left:142px;top:1961px">Enter Your Email Id :</div>
<div class="abs f-input" style="left:142px;top:2007px">Enter Your Email Id :</div>
<div class="abs f-btn">SUBSCRIBE</div>

<div class="abs f-head" style="left:484px;top:1873px">Contact Us</div>
<div class="abs f-text" style="left:484px;top:1919px">Feel free to contact us if you have any problems.</div>
<ul class="abs f-list" style="left:488px;top:1952px">
  <li>Address :42 Seabreeze Parade, PO BOX 7720,</li>
  <li>Email : www.cfag-clinic.com</li>
  <li>Fax : 08 5550 0182</li>
  <li>Phone : 08 5550 0147</li>
</ul>

<div class="abs f-head" style="left:808px;top:1873px">About Us</div>
<div class="abs f-text" style="left:808px;top:1914px;width:230px;line-height:20.5px">Lorem ipsum dolor sit amet, consectetur adipi scing elit. Vestibulum iaculis massa nec velit commodo lobortis.Quisque diam lacus, tincidunt vitae eros porta, sagittis rhoncus est. Quisque sed justo commodo lobortis.Quisque diam lacus, tincidunt vitae eros porta, sagittis rhoncus est. Quisque sed justo...........</div>

<div class="abs f-rule"></div>
<div class="abs f-text" style="left:142px;top:2124px">© Copy Rights 2014 - Colin Brasket .All rights reserved</div>
<div class="abs social" style="left:861px;top:2117px"></div>
<div class="abs social" style="left:903px;top:2117px"></div>
<div class="abs social" style="left:945px;top:2117px"></div>
<div class="abs social" style="left:987px;top:2117px"></div>
<div class="abs social" style="left:1029px;top:2117px"></div>
</body>
</html>
```